Exciting new aperitif brand needs a great label

Vel-Orin is a wonderful rich new premium-priced bitter aperitif, with a deep red colour, from a 100+ year old distillery (1890) near Turin in the Piedmont region of Italy. Inspired by Tessoni, it is perfectly formulated to elevate the classic Bravetti cocktail (and variations on it). It also goes perfectly in a Spritz or a long mixed drink with soda or tonic. The name Vel-Orin is derived from the French for 'peak' and the Italian word for 'love'.

The label, which should take inspiration from Tessoni, but be distinctively different, can incoporate any number of premium label embellishments (foil, embossing, textures etc) and should be no greater than 11cm (height) x 9cm (width) with any core imagery restricted to a width of c.7cm.

The attached mood board should act as inspiration and colour should largely be restricted to reds, blues, whites and perhaps orange. For completeness, the label should note that the ABV is 25% and the bottle size 70cl.

Target Market(s)

21-45yr olds - equal split female/male

Colors
0054AA
0677BA
7BADD7
CADEEF
E8F1F8
0094D4
00A9DD
6FCCEA
C7EBF8
E9F6FB
EE7325
F08F49
F5BC92
FAE3D3
FDF4ED
EB3D1F
EC4F4E
F09395
F8D3D4
FCEDEE

Requirements
Must have
• Great lettering design on the name Vel-Orin

```html
<!DOCTYPE html>
<html lang="en">
<head>
<meta charset="utf-8">
<title>Vel-Orin Aperitivo Labels</title>
<link rel="stylesheet" href="https://fonts.googleapis.com/css2?family=Cinzel:wght@700&family=Great+Vibes&family=Bodoni+Moda:wght@700&family=Libre+Caslon+Text&family=Oswald:wght@400&display=swap">
<style>
  :root {
    --stage: #08080a;
    --paper: #d9ebf8;
    --paper-line: #c3dcef;
    --gold: #f2b318;
    --gold-deep: #d99a10;
    --azure: #0a79c4;
    --azure-deep: #0867ad;
    --navy: #0c2d63;
    --navy-deep: #072252;
    --red: #d8281d;
    --white: #ffffff;
  }
  * { box-sizing: border-box; margin: 0; padding: 0; }
  html, body { width: 1200px; height: 1062px; overflow: hidden; background: var(--stage); }
  .stage { position: relative; width: 1200px; height: 1062px; }

  .label {
    position: absolute; top: 187px; width: 524px; height: 641px;
    background: var(--paper); overflow: hidden;
  }
  .label--azure { left: 51px; }
  .label--navy { left: 616px; }

  .label__pattern {
    position: absolute; inset: 0;
    background: radial-gradient(ellipse at 50% 50%, var(--paper) 30%, var(--paper-line) 100%);
    opacity: .6;
  }

  .bead-row {
    position: absolute; height: 6px;
    background: repeating-linear-gradient(90deg, var(--gold) 0 6px, transparent 6px 10px);
  }
  .bead-row--top { top: 11px; left: 10px; width: 504px; }
  .bead-row--bottom-left { top: 623px; left: 10px; width: 222px; }
  .bead-row--bottom-right { top: 623px; left: 345px; width: 169px; }
  .bead-row--bottom-left { width: 222px; left: 10px; }

  .region-flag { position: absolute; left: 222px; top: 39px; width: 78px; height: 51px; }

  .crest-ornament {
    position: absolute; left: 108px; top: 84px; width: 302px; height: 75px;
    background: radial-gradient(ellipse at 50% 60%, rgba(242,179,24,.55), rgba(242,179,24,.15) 70%, transparent 100%);
  }
  .crest-ornament__region {
    position: absolute; left: 0; right: 0; top: 12px; text-align: center;
    font-family: "Great Vibes", cursive; font-size: 24px; color: var(--gold-deep);
  }

  .name-band { position: absolute; left: 0; top: 160px; width: 524px; height: 240px; }

  .band-flourish {
    position: absolute; left: 217px; top: 205px; width: 88px; height: 20px; border-radius: 10px;
  }
  .label--azure .band-flourish { background: linear-gradient(90deg, transparent, rgba(255,255,255,.7), transparent); }
  .label--navy .band-flourish { background: linear-gradient(90deg, transparent, var(--gold), transparent); }

  .brand-name { font-family: "Cinzel", serif; font-weight: 700; }

  .abv, .volume {
    position: absolute; top: 462px;
    font-family: "Libre Caslon Text", serif; font-size: 17px; color: var(--navy);
  }
  .abv { left: 36px; }
  .volume { left: 434px; }

  .category {
    position: absolute; left: 112px; width: 300px; top: 424px; text-align: center;
    font-family: "Bodoni Moda", serif; font-weight: 700; font-size: 64px; line-height: 1;
    color: var(--red); transform: scaleX(.62); transform-origin: center;
  }
  .descriptor {
    position: absolute; left: 150px; width: 224px; top: 496px; text-align: center;
    font-family: "Oswald", sans-serif; font-size: 22px; line-height: 1;
    transform: scaleX(.78);
  }
  .label--azure .descriptor { color: var(--navy); }
  .label--navy .descriptor { color: var(--red); }

  .floral-corner {
    position: absolute; top: 497px; width: 121px; height: 114px;
    background: radial-gradient(circle at 40% 55%, rgba(242,179,24,.6), rgba(216,40,29,.25) 60%, transparent 80%);
  }
  .floral-corner--left { left: 31px; }
  .floral-corner--right { left: 372px; }

  .origin-badge {
    position: absolute; left: 187px; top: 582px; width: 151px; height: 47px;
    border: 2px solid var(--gold); outline: 1px solid var(--white); outline-offset: -5px;
    text-align: center; color: var(--white); font-family: "Libre Caslon Text", serif;
  }
  .label--azure .origin-badge { background: linear-gradient(90deg, var(--navy-deep), #1a4d8f 50%, var(--navy-deep)); }
  .label--navy .origin-badge { background: var(--red); }
  .origin-badge__line { display: block; font-size: 10px; letter-spacing: 2.5px; margin-top: 6px; }
  .origin-badge__country { display: block; font-size: 18px; letter-spacing: 4px; line-height: 20px; }
</style>
</head>
<body>
<main class="stage">

  <section class="label label--azure">
    <div class="label__pattern" role="img" aria-label="Embossed interlaced knotwork pattern"></div>
    <div class="bead-row bead-row--top"></div>

    <svg class="region-flag" viewBox="0 0 78 51" aria-label="Piedmont flag">
      <rect x="1" y="1" width="76" height="49" fill="var(--navy)"/>
      <rect x="4" y="4" width="70" height="43" fill="var(--red)"/>
      <rect x="34" y="8" width="10" height="37" fill="var(--white)"/>
      <rect x="12" y="21" width="54" height="10" fill="var(--white)"/>
      <rect x="20" y="6" width="38" height="3" fill="var(--navy)"/>
    </svg>

    <div class="crest-ornament" role="img" aria-label="Gold and red baroque crest flourish">
      <div class="crest-ornament__region">Piedmont</div>
    </div>

    <svg class="name-band" viewBox="0 160 524 240">
      <path d="M0,191 H150 C170,191 175,168 200,168 H324 C349,168 354,191 374,191 H524 V367 H374 C354,367 349,390 324,390 H200 C175,390 170,367 150,367 H0 Z"
            fill="var(--azure)" stroke="var(--gold)" stroke-width="5"/>
      <path d="M0,197 H524 M0,361 H524" stroke="var(--azure-deep)" stroke-width="2"/>
      <text class="brand-name" x="48" y="316" font-size="92" textLength="427" lengthAdjust="spacingAndGlyphs" fill="var(--navy)">VEL-ORIN</text>
      <path id="arc-azure" d="M195,348 Q262,380 330,348" fill="none"/>
      <text font-family="Libre Caslon Text, serif" font-size="13" letter-spacing="4" fill="var(--white)">
        <textPath href="#arc-azure" startOffset="50%" text-anchor="middle">Since 1890</textPath>
      </text>
    </svg>
    <div class="band-flourish" role="img" aria-label="Small scroll flourish"></div>

    <div class="abv">25% vol.</div>
    <div class="category">APERETIVO</div>
    <div class="volume">700 ml.</div>
    <div class="descriptor">premium-priced bitter</div>

    <div class="floral-corner floral-corner--left" role="img" aria-label="Gold scrollwork with red flowers"></div>
    <div class="floral-corner floral-corner--right" role="img" aria-label="Gold scrollwork with red flowers"></div>

    <div class="bead-row bead-row--bottom-left"></div>
    <div class="origin-badge">
      <span class="origin-badge__line">PRODUCED BY</span>
      <span class="origin-badge__country">ITALY</span>
    </div>
    <div class="bead-row bead-row--bottom-right"></div>
  </section>

  <section class="label label--navy">
    <div class="label__pattern" role="img" aria-label="Embossed interlaced knotwork pattern"></div>
    <div class="bead-row bead-row--top"></div>

    <svg class="region-flag" viewBox="0 0 78 51" aria-label="Piedmont flag">
      <rect x="1" y="1" width="76" height="49" fill="var(--navy)"/>
      <rect x="4" y="4" width="70" height="43" fill="var(--red)"/>
      <rect x="34" y="8" width="10" height="37" fill="var(--white)"/>
      <rect x="12" y="21" width="54" height="10" fill="var(--white)"/>
      <rect x="20" y="6" width="38" height="3" fill="var(--navy)"/>
    </svg>

    <div class="crest-ornament" role="img" aria-label="Gold and red baroque crest flourish">
      <div class="crest-ornament__region">Piedmont</div>
    </div>

    <svg class="name-band" viewBox="0 160 524 240">
      <path d="M0,191 H150 C170,191 175,168 200,168 H324 C349,168 354,191 374,191 H524 V367 H374 C354,367 349,390 324,390 H200 C175,390 170,367 150,367 H0 Z"
            fill="var(--navy)" stroke="var(--gold)" stroke-width="5"/>
      <path d="M0,197 H524 M0,361 H524" stroke="var(--navy-deep)" stroke-width="2"/>
      <text class="brand-name" x="48" y="316" font-size="92" textLength="427" lengthAdjust="spacingAndGlyphs" fill="var(--white)">VEL-ORIN</text>
      <path id="arc-navy" d="M195,348 Q262,380 330,348" fill="none"/>
      <text font-family="Libre Caslon Text, serif" font-size="13" letter-spacing="4" fill="var(--white)">
        <textPath href="#arc-navy" startOffset="50%" text-anchor="middle">Since 1890</textPath>
      </text>
    </svg>
    <div class="band-flourish" role="img" aria-label="Small gold fan flourish"></div>

    <div class="abv">25% vol.</div>
    <div class="category">APERETIVO</div>
    <div class="volume">700 ml.</div>
    <div class="descriptor">premium-priced bitter</div>

    <div class="floral-corner floral-corner--left" role="img" aria-label="Gold scrollwork with red flowers"></div>
    <div class="floral-corner floral-corner--right" role="img" aria-label="Gold scrollwork with red flowers"></div>

    <div class="bead-row bead-row--bottom-left"></div>
    <div class="origin-badge">
      <span class="origin-badge__line">PRODUCED BY</span>
      <span class="origin-badge__country">ITALY</span>
    </div>
    <div class="bead-row bead-row--bottom-right"></div>
  </section>

</main>
</body>
</html>
```